Corporate Business Card

Very professional, Modern, Not to busy, include phone address email, website
(253) 617-4930, 18761 52nd Avenue S, Kent, WA 98047, martin@plumlinegroup.com, varkoworks.com

Target Market(s)

Manufacturing

Industry/Entity Type

Aero, machining, manufacturing, Off road racing

Contact Information for Business Card

Phone, address email, website

```html
<!DOCTYPE html>
<html lang="en">
<head>
<meta charset="utf-8">
<title>Varko Works – Business Card</title>
<link href="https://fonts.googleapis.com/css2?family=Poppins:wght@400;600&display=swap" rel="stylesheet">
<style>
  :root {
    --backdrop: #3b3b3b;
    --brand-red: #d2232a;
    --brand-navy: #1c3a7a;
    --silver: #d6d6d6;
    --paper: #ffffff;
    --ink: #1d1d1d;
  }
  * { box-sizing: border-box; margin: 0; padding: 0; }
  html, body {
    width: 1200px; height: 904px; overflow: hidden;
    background: var(--backdrop);
    font-family: "Poppins", sans-serif;
  }
  .card {
    position: absolute;
    width: 560px; height: 320px;
    overflow: hidden;
    box-shadow: 0 10px 24px rgba(0,0,0,.45);
  }
  /* Front side */
  .card-front {
    left: 90px; top: 80px;
    background: var(--brand-red);
  }
  .front-name {
    position: absolute; left: 0; right: 0; top: 118px;
    text-align: center;
    font-weight: 600; font-size: 54px; letter-spacing: 1px;
    color: var(--silver);
  }
  .front-rule {
    position: absolute; left: 110px; top: 200px;
    width: 200px; height: 3px; background: var(--silver);
  }
  /* Back side */
  .card-back {
    left: 550px; top: 484px;
    background: var(--paper);
    color: var(--ink);
  }
  .back-name {
    position: absolute; right: 30px; top: 38px;
    font-weight: 600; font-size: 34px;
    color: var(--brand-navy);
  }
  .back-rule {
    position: absolute; right: 178px; top: 92px;
    width: 170px; height: 2px; background: var(--brand-navy);
  }
  .address {
    position: absolute; left: 34px; top: 112px;
    font-size: 15px; line-height: 1.35;
  }
  .contacts {
    position: absolute; left: 34px; top: 206px;
    list-style: none;
    font-size: 15px; line-height: 1;
  }
  .contacts li {
    display: flex; align-items: center; gap: 10px;
    margin-bottom: 9px;
  }
  .contacts svg { width: 14px; height: 14px; fill: var(--brand-red); flex: none; }
  .bands { position: absolute; left: 0; bottom: 0; width: 560px; height: 40px; }
</style>
</head>
<body>

<section class="card card-front">
  <div class="front-name">Varko Works</div>
  <div class="front-rule"></div>
</section>

<section class="card card-back">
  <div class="back-name">Varko Works</div>
  <div class="back-rule"></div>

  <p class="address">18761 52nd Avenue<br>S, Kent, WA 98047</p>

  <ul class="contacts">
    <li>
      <svg viewBox="0 0 24 24" aria-hidden="true"><path d="M6.6 10.8a15.1 15.1 0 0 0 6.6 6.6l2.2-2.2a1 1 0 0 1 1-.25 11.4 11.4 0 0 0 3.6.57 1 1 0 0 1 1 1V20a1 1 0 0 1-1 1A17 17 0 0 1 3 4a1 1 0 0 1 1-1h3.5a1 1 0 0 1 1 1c0 1.25.2 2.45.57 3.57a1 1 0 0 1-.25 1z"/></svg>
      (253) 617-4930
    </li>
    <li>
      <svg viewBox="0 0 24 24" aria-hidden="true"><path d="M2 5h20v14H2z M2 5l10 8 10-8" stroke="#fff" stroke-width="1.5"/></svg>
      martin@plumlinegroup.com
    </li>
    <li>
      <svg viewBox="0 0 24 24" aria-hidden="true"><circle cx="12" cy="12" r="10"/><path d="M2 12h20M12 2c3 3 3 17 0 20M12 2c-3 3-3 17 0 20" stroke="#fff" stroke-width="1.3" fill="none"/></svg>
      www.varkoworks.com
    </li>
  </ul>

  <svg class="bands" viewBox="0 0 560 40" preserveAspectRatio="none" aria-hidden="true">
    <polygon points="0,24 398,24 384,40 0,40" fill="var(--brand-navy)"/>
    <polygon points="418,12 560,12 560,40 394,40" fill="var(--brand-red)"/>
  </svg>
</section>

</body>
</html>
```